Web Design for an Innovative Life Science Marketplace

IMPORTANT:
The software is called CS-Cart. It has capabilities and limitations with design features in the software. There is a certain framework that needs to be followed. It is PHP and Linux. It may require add-ons for your design, so please be specific with what is required. It’s preferred the designer has CS-Cart knowledge/experience.

Key Requirements
1. I’d like the design to include an implemented/recommended CS-Cart theme that is consistent with our branding (see the marketing collateral and logo).
2. I then need the additional design changes to that theme to create the below web pages.
3. All designs should be consistent with our branding. All pictures should either be computer generated (clip art-like) or pictures of happy patients. What is a happy patient? Close up photo of someone healthy, happy, and experiencing/enjoying life. Not someone in a hospital or getting care. Please see examples already on the site.

Please see the attached Web Design details in the word document. That document is important to complete the design.

```html
<!DOCTYPE html>
<html lang="en">
<head>
<meta charset="utf-8">
<title>Verdeloop — Life Sciences Marketplace</title>
<link rel="stylesheet" href="https://fonts.googleapis.com/css2?family=Montserrat:wght@400;500;600;700;800&family=Open+Sans:wght@400;600&display=swap">
<style>
:root{
  --teal:#2f7b6f;
  --lime:#8cc63f;
  --green:#5aa54a;
  --ink:#222;
  --muted:#666;
  --card:#f0f0f0;
  --dark:#1d1f1f;
  --white:#fff;
  --grad:linear-gradient(90deg,var(--teal) 0%,var(--green) 55%,var(--lime) 100%);
}
*{box-sizing:border-box;margin:0;padding:0}
html,body{width:1200px;height:3261px;overflow:hidden}
body{position:relative;font-family:"Open Sans",Arial,sans-serif;color:var(--ink);background:var(--white)}
.abs{position:absolute}
.heading{font-family:"Montserrat",Arial,sans-serif;font-weight:700;letter-spacing:1px}

/* top bar + header */
.topbar{left:0;top:0;width:1200px;height:48px;background:var(--lime)}
.topbar-icons{right:240px;top:12px;display:flex;gap:26px}
.contact-tab{right:80px;top:0;width:190px;height:52px;background:var(--teal);border-radius:0 0 14px 14px;color:#fff;font-family:"Montserrat",sans-serif;font-weight:600;font-size:20px;display:flex;align-items:center;justify-content:center}
.header{left:0;top:48px;width:1200px;height:109px;background:#fff}
.brand{left:78px;top:42px;display:flex;align-items:center;gap:10px;font-family:"Montserrat",sans-serif;font-weight:700;font-size:28px;color:var(--green)}
.brand-dot{width:34px;height:34px;border-radius:50%;background:var(--teal)}
.nav{left:327px;top:42px;display:flex;gap:27px;font-family:"Montserrat",sans-serif;font-size:15.5px;color:#444;text-transform:uppercase}
.nav .active{color:var(--green)}

/* hero */
.hero{left:0;top:157px;width:1200px;height:604px;background:radial-gradient(circle at 70% 25%,#f4d9a8 0%,#c99a6a 25%,#7e6a58 55%,#4d4a44 100%)}
.hero-title{left:0;top:260px;width:1200px;text-align:center;color:#fff;font-family:"Montserrat",sans-serif;font-weight:600;font-size:46px;line-height:58px}
.tagline-band{left:0;top:761px;width:1200px;height:102px;background:var(--grad)}
.tagline{left:80px;top:780px;width:640px;color:#fff;font-size:17px;line-height:28px}
.pill{background:#fff;border-radius:40px;display:flex;align-items:center;justify-content:center;gap:14px;font-family:"Montserrat",sans-serif;font-weight:600;color:var(--lime);text-transform:uppercase}
.pill-dot{width:40px;height:40px;border-radius:50%;border:3px solid var(--teal)}
.preregister{left:883px;top:786px;width:240px;height:52px;font-size:19px}

/* who should join */
.section-title{left:0;width:1200px;text-align:center;font-family:"Montserrat",sans-serif;font-weight:700;font-size:40px;letter-spacing:2px}
.join-card{top:1050px;width:322px;height:228px;background:var(--card);border-radius:6px;text-align:center}
.join-card::before{content:"";position:absolute;left:128px;top:0;width:66px;height:4px;background:var(--lime)}
.join-card svg{margin-top:22px}
.join-card h3{font-family:"Montserrat",sans-serif;font-weight:500;font-size:23px;margin-top:12px;color:#333}
.join-card p{font-size:14.5px;line-height:25px;color:var(--muted);margin:10px 24px 0}

/* about */
.about{left:0;top:1374px;width:1200px;height:522px;background:var(--grad)}
.about-ring{left:86px;top:1428px;width:414px;height:414px;border-radius:50%;background:rgba(255,255,255,.12)}
.about-ring2{left:120px;top:1462px;width:346px;height:346px;border-radius:50%;background:rgba(255,255,255,.25)}
.about-photo{left:141px;top:1483px;width:304px;height:304px;border-radius:50%;background:radial-gradient(circle at 50% 40%,#e9c9a6,#b07a4e 55%,#5f7a47)}
.about-copy{left:613px;top:1464px;width:500px;color:#fff}
.about-copy h2{font-size:42px;margin-bottom:22px}
.about-copy p{font-size:14.5px;line-height:27px;margin-bottom:14px}
.readmore{left:613px;top:1738px;width:220px;height:52px;font-size:19px}

/* marketing */
.marketing{left:0;top:1896px;width:1200px;height:332px;background:linear-gradient(90deg,#2d2723,#5b4a3e 30%,#3d332c 60%,#2a2420)}
.marketing-shade{left:0;top:1896px;width:1200px;height:332px;background:rgba(20,20,20,.45)}
.marketing-copy{left:200px;top:1964px;width:800px;text-align:center;color:#fff}
.marketing-copy h2{font-size:40px;letter-spacing:2px}
.marketing-copy p{font-size:14.5px;line-height:27px;margin-top:16px}
.btn-white{top:2102px;height:52px;font-size:19px}

/* products */
.product{width:380px}
.product h4{font-family:"Montserrat",sans-serif;font-weight:500;font-size:22px;color:#333}
.product p{font-size:14.5px;line-height:27px;color:var(--muted);margin-top:10px}
.product.left{text-align:right}
.p-icon{width:114px;height:114px;border-radius:50%;background:linear-gradient(135deg,var(--lime),var(--teal));border:5px solid #e6efe0;display:flex;align-items:center;justify-content:center}

/* promise */
.promise-band{left:0;top:2804px;width:1200px;height:103px;background:var(--grad)}
.promise-title{left:80px;top:2836px;color:#fff;font-size:35px;letter-spacing:1.5px}
.promise-quote{left:597px;top:2826px;width:540px;color:#fff;font-size:17px;line-height:29px}

/* footer */
.footer{left:0;top:2907px;width:1200px;height:289px;background:linear-gradient(90deg,#1e2020,#2c2a28 55%,#3a3430 80%,#222)}
.foot-col{top:2954px;color:#fff}
.foot-col h5{font-family:"Montserrat",sans-serif;font-weight:600;font-size:22px;margin-bottom:18px}
.foot-col li{list-style:none;font-size:14.5px;line-height:38.5px;display:flex;align-items:center;gap:16px}
.foot-col li::before{content:"";width:10px;height:10px;border-radius:50%;background:#fff}
.foot-col.contact li::before{display:none}
.foot-col.contact li{line-height:24px;margin-bottom:14px;align-items:flex-start}
.copyright{left:0;top:3196px;width:1200px;height:65px;background:var(--lime);color:#333;font-size:15px;display:flex;align-items:center;justify-content:center}
</style>
</head>
<body>

<div class="abs topbar"></div>
<div class="abs topbar-icons">
  <svg width="22" height="22" viewBox="0 0 22 22" fill="none" stroke="#fff" stroke-width="2.5"><circle cx="9" cy="9" r="7"/><path d="M14 14l6 6"/></svg>
  <svg width="26" height="22" viewBox="0 0 26 22" fill="none" stroke="#fff" stroke-width="2.2"><path d="M2 3h4l3 13h12l3-10H8"/><circle cx="11" cy="19" r="1.5"/><circle cx="19" cy="19" r="1.5"/></svg>
  <svg width="20" height="22" viewBox="0 0 20 22" fill="#fff"><circle cx="10" cy="6" r="5"/><path d="M1 21c0-6 4-9 9-9s9 3 9 9z"/></svg>
</div>
<div class="abs contact-tab">CONTACT US</div>

<header class="abs header">
  <div class="abs brand"><span class="brand-dot"></span>VERDELOOP</div>
  <nav class="abs nav">
    <span class="active">Home</span><span>About Us</span><span>Why Verdeloop?</span><span>Our Partners</span><span>White Paper</span><span>Quality Policy</span>
  </nav>
</header>

<section>
  <div class="abs hero" role="img" aria-label="Photo of a smiling young woman in a hat on a sunny hillside"></div>
  <svg class="abs" style="left:400px;top:280px" width="400" height="360" viewBox="0 0 400 360" fill="none" stroke="rgba(255,255,255,.7)" stroke-width="2"><circle cx="200" cy="180" r="170"/><circle cx="195" cy="190" r="150" stroke-width="1.2"/></svg>
  <h1 class="abs hero-title">Join the Circular<br>Supply Chain</h1>
  <div class="abs tagline-band"></div>
  <svg class="abs" style="left:0;top:862px" width="1200" height="52" viewBox="0 0 1200 52"><path d="M0 0H1200V1C900 1 650 10 600 52 550 10 300 1 0 1z" fill="#65a94b"/></svg>
  <p class="abs tagline">“A virtual multi-vendor marketplace and for the life sciences community to connect and transact before and after-market materials and equipment”</p>
  <div class="abs pill preregister">Pre- Register <span class="pill-dot"></span></div>
</section>

<section>
  <h2 class="abs section-title" style="top:962px">WHO SHOULD JOIN?</h2>
  <div class="abs join-card" style="left:78px">
    <svg width="74" height="74" viewBox="0 0 74 74" fill="none" stroke="#5aa54a" stroke-width="3"><circle cx="37" cy="37" r="30" stroke-dasharray="40 8"/><circle cx="37" cy="37" r="14" stroke="#2f7b6f"/><circle cx="37" cy="37" r="5"/></svg>
    <h3>Manufacturers</h3>
    <p>Create an Account in Minutes to Sell/Buy Excess or Obsolete Materials and Equipment</p>
  </div>
  <div class="abs join-card" style="left:439px">
    <svg width="74" height="74" viewBox="0 0 74 74" fill="none" stroke="#5aa54a" stroke-width="3"><circle cx="22" cy="20" r="8"/><circle cx="52" cy="20" r="8" stroke="#2f7b6f"/><path d="M8 52c0-12 6-18 14-18s14 6 14 18M38 52c0-12 6-18 14-18s14 6 14 18" /><path d="M10 60h54"/></svg>
    <h3>Researchers</h3>
    <p>Sell/Buy Low-Cost Materials and Receive Donations</p>
  </div>
  <div class="abs join-card" style="left:800px">
    <svg width="74" height="74" viewBox="0 0 74 74" fill="none" stroke="#5aa54a" stroke-width="3"><circle cx="20" cy="14" r="7"/><path d="M10 30h20v22H10zM14 52v16M26 52v16"/><path d="M38 36h6l4 18h18l4-14H46" stroke="#2f7b6f"/><circle cx="52" cy="62" r="3"/><circle cx="64" cy="62" r="3"/></svg>
    <h3>Original Suppliers</h3>
    <p>Market Your Products Across a Broad Life Sciences Network</p>
  </div>
</section>

<section>
  <div class="abs about"></div>
  <div class="abs about-ring"></div>
  <div class="abs about-ring2"></div>
  <div class="abs about-photo" role="img" aria-label="Photo of two laughing older women sitting outdoors"></div>
  <div class="abs about-copy">
    <h2 class="heading">ABOUT US</h2>
    <p>We are a private and virtual B2B marketplace and consortium for life science manufacturers, researchers, and vendors to sell, purchase, and donate before and aftermarket materials and equipment as well as collaborate on non-financial ventures.</p>
    <p>We are in the developmental phase of our platform working with some of the most trusted and best industry partners. We are tentatively scheduled for an exclusive launch before the end of 2018.</p>
  </div>
  <div class="abs pill readmore">Read More <span class="pill-dot"></span></div>
</section>

<section>
  <div class="abs marketing" role="img" aria-label="Strip of close-up photos of smiling people"></div>
  <div class="abs marketing-shade"></div>
  <div class="abs marketing-copy">
    <h2 class="heading">MAKRKETING MATERIALS</h2>
    <p>Lorem Ipsum is simply dummy text of the printing and typesetting industry. Lorem Ipsum has been the industry's standard dummy text ever since the 1500s, when an unknown printer took a galley of type.</p>
  </div>
  <div class="abs pill btn-white" style="left:262px;width:340px">Read Our White Paper <span class="pill-dot"></span></div>
  <div class="abs pill btn-white" style="left:627px;width:314px">Read Our Brochure <span class="pill-dot"></span></div>
</section>

<section>
  <h2 class="abs section-title" style="top:2286px">PRODUCTS</h2>
  <svg class="abs" style="left:549px;top:2452px" width="100" height="110" viewBox="0 0 100 110" stroke="#e2e2e2" stroke-width="2"><path d="M50 0v110M0 55h100"/></svg>

  <div class="abs product left" style="left:38px;top:2363px"><h4>Raw Materials</h4><p>Consumable and starting materials for API and intermediate manufacturing or research.</p></div>
  <div class="abs p-icon" style="left:450px;top:2361px"><svg width="50" height="50" viewBox="0 0 50 50" fill="none" stroke="#fff" stroke-width="2.5"><path d="M8 10h26l8 8v24H8z"/><path d="M14 24h22M14 32h22"/></svg></div>
  <div class="abs p-icon" style="left:634px;top:2361px"><svg width="50" height="50" viewBox="0 0 50 50" fill="#fff"><path d="M6 20h10a5 5 0 1 1 10 0h10v10a5 5 0 1 1 0 10v6H6V36a5 5 0 1 0 0-10z"/></svg></div>
  <div class="abs product" style="left:789px;top:2363px"><h4>Parts</h4><p>Components of a modular system used for LS applications</p></div>

  <div class="abs product left" style="left:38px;top:2558px"><h4>Equipment</h4><p>End item systems manufactured for LS applications</p></div>
  <div class="abs p-icon" style="left:450px;top:2541px"><svg width="50" height="50" viewBox="0 0 50 50" fill="none" stroke="#fff" stroke-width="3"><circle cx="25" cy="25" r="14" stroke-dasharray="7 4"/><circle cx="25" cy="25" r="6"/></svg></div>
  <div class="abs p-icon" style="left:634px;top:2541px"><svg width="50" height="50" viewBox="0 0 50 50" fill="#fff"><circle cx="25" cy="10" r="6"/><circle cx="10" cy="36" r="6"/><circle cx="40" cy="36" r="6"/><circle cx="25" cy="28" r="14" fill="none" stroke="#fff" stroke-width="2.5"/></svg></div>
  <div class="abs product" style="left:789px;top:2558px"><h4>Collaborative Relationships</h4><p>Safety Stock Agreements, Advertising/Selling/ Donating Capacity, joint supplier audits, etc.</p></div>
</section>

<section>
  <svg class="abs" style="left:0;top:2749px" width="1200" height="56" viewBox="0 0 1200 56"><path d="M0 56C300 55 550 45 600 0 650 45 900 55 1200 56z" fill="#65a94b"/></svg>
  <div class="abs promise-band"></div>
  <h2 class="abs heading promise-title">OUR PROMISE</h2>
  <p class="abs promise-quote">“A greener, more cost-efficient, and quality-driven supply chain through a collaborative life sciences marketplace”</p>
</section>

<footer>
  <div class="abs footer" role="img" aria-label="Dimmed photo of a smiling person behind the footer"></div>
  <div class="abs foot-col" style="left:80px"><h5>Our Marketplace</h5><ul><li>About us</li><li>How it Works</li><li>Our Partners</li><li>White Paper</li></ul></div>
  <div class="abs foot-col" style="left:441px"><h5>Customer service</h5><ul><li>Quality Policy</li><li>Privacy Policy</li><li>Sign in</li></ul></div>
  <div class="abs foot-col contact" style="left:803px"><h5>Contact Info</h5><ul>
    <li><svg width="20" height="24" viewBox="0 0 20 24" fill="none" stroke="#fff" stroke-width="2"><path d="M10 22s8-8 8-13a8 8 0 0 0-16 0c0 5 8 13 8 13z"/><circle cx="10" cy="9" r="3"/></svg><span>240 Harbor Row STE 310<br>Riverton, OH 44120</span></li>
    <li><svg width="22" height="22" viewBox="0 0 22 22" fill="none" stroke="#fff" stroke-width="2"><path d="M4 2h5l2 5-3 2a12 12 0 0 0 5 5l2-3 5 2v5c0 1-1 2-2 2A18 18 0 0 1 2 4c0-1 1-2 2-2z"/></svg><span>+1 800-555-0142</span></li>
    <li><svg width="22" height="18" viewBox="0 0 22 18" fill="none" stroke="#fff" stroke-width="2"><rect x="1" y="1" width="20" height="16"/><path d="M1 1l10 9 10-9"/></svg><span>hello@verdeloop.example</span></li>
  </ul></div>
  <div class="abs copyright">©VERDELOOP, 2018 · All Rights Reserved.</div>
</footer>

</body>
</html>
```